HearthMile business card and stationary design

We are looking for a simple yet elegant design for our mortgage company business card and stationary.

The card should include:
Name (Marcus Pell)
Title (CEO)
Phone Number (732-555-0182)
Address (48 Birchwell Court, Suite 314, Larkfield, NJ 08123)
Email (email@hearthmile.example)
"NMLS" i.e. (NMLS 61947)
"Company NMLS" (Company NMLS 274615)

Contact Information for Business Card

See above

```html
<!DOCTYPE html>
<html lang="en">
<head>
<meta charset="utf-8">
<title>HearthMile Business Card</title>
<link rel="stylesheet" href="https://fonts.googleapis.com/css2?family=Montserrat:wght@500;600;700&family=Roboto:wght@400;500&display=swap">
<style>
  :root {
    --bg: #e9eaec;
    --navy: #1b2735;
    --blue: #29a8e0;
    --white: #ffffff;
    --ink: #1e2229;
    --rule: #2a3140;
  }
  * { box-sizing: border-box; margin: 0; padding: 0; }
  html, body { width: 1200px; height: 900px; overflow: hidden; }
  body {
    background: var(--bg);
    position: relative;
    font-family: "Roboto", Arial, sans-serif;
  }
  .card {
    position: absolute;
    left: 285px;
    width: 630px;
    height: 360px;
    box-shadow: 0 6px 18px rgba(0,0,0,0.12);
    overflow: hidden;
  }
  .card--front { top: 60px; background: var(--navy); }
  .card--back { top: 480px; background: var(--white); }

  .wordmark {
    font-family: "Montserrat", Arial, sans-serif;
    font-weight: 600;
    color: var(--blue);
    letter-spacing: -0.5px;
    white-space: nowrap;
    position: absolute;
  }
  .card--front .wordmark {
    font-size: 82px;
    left: 0; right: 0;
    top: 128px;
    text-align: center;
  }
  .card--back .wordmark {
    font-size: 44px;
    left: 48px;
    top: 76px;
  }

  .edge-tab {
    position: absolute;
    right: 0;
    top: 44px;
    width: 14px;
    height: 56px;
    background: var(--navy);
  }
  .holder-name {
    position: absolute;
    right: 60px;
    top: 112px;
    font-family: "Montserrat", Arial, sans-serif;
    font-weight: 700;
    font-size: 28px;
    letter-spacing: 0.5px;
    color: var(--navy);
    white-space: nowrap;
  }
  .holder-name .surname { color: var(--blue); }
  .divider {
    position: absolute;
    left: 40px;
    right: 60px;
    top: 160px;
    height: 1.5px;
    background: var(--rule);
  }
  .holder-title {
    position: absolute;
    right: 60px;
    top: 166px;
    font-size: 14px;
    color: var(--ink);
    letter-spacing: 0.5px;
  }
  .licences {
    position: absolute;
    right: 40px;
    top: 196px;
    text-align: right;
    font-size: 15px;
    line-height: 22px;
    color: var(--ink);
  }
  .contact {
    position: absolute;
    left: 44px;
    top: 180px;
    font-size: 17px;
    line-height: 25px;
    color: var(--ink);
    list-style: none;
  }
  .contact li { display: flex; align-items: center; white-space: nowrap; }
  .contact .icon { width: 15px; height: 15px; margin-right: 7px; flex: none; }
</style>
</head>
<body>
  <section class="card card--front" aria-label="Card front">
    <div class="wordmark">HearthMile</div>
  </section>

  <section class="card card--back" aria-label="Card back">
    <div class="edge-tab"></div>
    <div class="wordmark">HearthMile</div>
    <div class="holder-name">MARCUS <span class="surname">PELL</span></div>
    <div class="divider"></div>
    <div class="holder-title">CEO</div>

    <ul class="contact">
      <li>48 Birchwell Court, Suite 314</li>
      <li>Larkfield, NJ 08123</li>
      <li>
        <svg class="icon" viewBox="0 0 16 16" aria-hidden="true"><path fill="#29a8e0" d="M3.5 1.5l2.5 0 1.2 3.2-1.6 1.2c.8 1.8 2.2 3.2 4 4l1.2-1.6 3.2 1.2v2.5c0 .9-.8 1.6-1.7 1.5C6.6 13 3 9.4 2 4.2 1.9 3.3 2.6 1.5 3.5 1.5z"/></svg>
        732-555-0182
      </li>
      <li>
        <svg class="icon" viewBox="0 0 16 16" aria-hidden="true"><rect x="1" y="3.5" width="14" height="9.5" rx="1.2" fill="#29a8e0"/><path d="M1.5 4.2L8 9l6.5-4.8" fill="none" stroke="#fff" stroke-width="1.3"/></svg>
        email@hearthmile.example
      </li>
      <li>
        <svg class="icon" viewBox="0 0 16 16" aria-hidden="true"><circle cx="8" cy="8" r="6.5" fill="none" stroke="#29a8e0" stroke-width="1.6"/><ellipse cx="8" cy="8" rx="2.6" ry="6.5" fill="none" stroke="#29a8e0" stroke-width="1.2"/><path d="M1.8 8h12.4" stroke="#29a8e0" stroke-width="1.2"/></svg>
        www.hearthmile.example
      </li>
    </ul>

    <div class="licences">
      <div>NMLS 61947</div>
      <div>Company NMLS 274615</div>
    </div>
  </section>
</body>
</html>
```